Upmarket Dessert Lounge needs a Business Card Design

We are an upmarket dessert lounge needing a business card to match our image.

We want something that is simple yet beautiful, feminine, classy, sophisticated and elegant. We want it to stand out and don't mind if it is bold.

The design should include our logo and colours of red or maroon with gold highlights. We don't mind if black is used.

Marlow & Quince

Target Market(s)

For those who like to indulge or treat themselves and give in to their temptations on good quality desserts.

Industry/Entity Type

Business

Requirements
Must have
• Must include our logo and our name

Marlow & Quince

M & Q

```html
<!DOCTYPE html>
<html lang="en">
<head>
<meta charset="utf-8">
<title>Marlow &amp; Quince — Business Card</title>
<link rel="stylesheet" href="https://fonts.googleapis.com/css2?family=Great+Vibes&family=Lato:wght@300;400&display=swap">
<style>
  :root {
    --maroon: #7a1416;
    --gold: #fdd197;
    --cocoa: #a55e51;
    --paper: #ffffff;
    --canvas: #ffffff;
  }
  * { margin: 0; padding: 0; box-sizing: border-box; }
  html, body {
    width: 1200px; height: 900px; overflow: hidden;
    background: var(--canvas);
  }
  .stage { position: relative; width: 1200px; height: 900px; }
  .card {
    position: absolute; top: 92px;
    width: 464px; height: 716px;
    background: var(--paper);
    box-shadow: 3px 4px 8px rgba(0,0,0,0.18);
    overflow: hidden;
  }
  .card--front { left: 37px; border: 1px solid #e2e2e2; }
  .card--back { left: 692px; }
  .card__art { position: absolute; inset: 0; width: 100%; height: 100%; }

  .monogram {
    position: absolute; left: 43px; top: 76px; width: 152px;
    text-align: center;
    font-family: "Lato", sans-serif; font-weight: 400;
    font-size: 40px; line-height: 48px; color: var(--gold); letter-spacing: 1px;
  }
  .tagline {
    position: absolute; left: 52px; top: 192px;
    font-family: "Great Vibes", cursive;
    font-size: 46px; line-height: 50px; color: var(--gold);
  }
  .tagline span { display: block; }
  .tagline span + span { padding-left: 58px; }

  .contact {
    position: absolute; right: 38px; top: 610px;
    text-align: right; font-style: normal;
    font-family: "Lato", sans-serif; font-weight: 300;
    font-size: 21px; line-height: 29px; color: var(--maroon);
  }

  .wordmark {
    position: absolute; left: 40px; width: 384px; top: 544px;
    text-align: center;
    font-family: "Lato", sans-serif; font-weight: 400;
    font-size: 28px; line-height: 36px; color: var(--gold); letter-spacing: 1px;
  }
  .website {
    position: absolute; left: 0; width: 100%; top: 662px;
    text-align: center;
    font-family: "Lato", sans-serif; font-weight: 400;
    font-size: 22px; line-height: 28px; color: var(--gold);
  }
</style>
</head>
<body>
<main class="stage">

  <section class="card card--front" aria-label="Card front">
    <svg class="card__art" viewBox="0 0 464 716">
      <defs>
        <radialGradient id="goldGlow">
          <stop offset="0" stop-color="#fdd197" stop-opacity="0.9"/>
          <stop offset="1" stop-color="#fdd197" stop-opacity="0"/>
        </radialGradient>
      </defs>
      <path class="field" aria-hidden="true" fill="var(--maroon)"
        d="M0,0 H464 V170 C464,300 380,355 260,362 C160,368 60,400 0,472 Z"/>
      <path class="field-edge" aria-hidden="true" fill="none" stroke="var(--gold)" stroke-width="7"
        d="M0,472 C60,400 160,368 260,362 C380,355 464,300 464,170"/>
      <g role="img" aria-label="Gold spiral swirl ornament">
        <circle cx="318" cy="113" r="62" fill="url(#goldGlow)"/>
      </g>
      <g role="img" aria-label="Large gold spiral swirl ornament">
        <circle cx="182" cy="490" r="110" fill="url(#goldGlow)"/>
      </g>
    </svg>

    <div class="monogram">M &amp; Q</div>
    <p class="tagline"><span>Dessert</span><span>Specialists</span></p>
    <address class="contact">
      Marlow 01632 960114<br>
      Quince 01632 960587<br>
      hello@marlowquince.com
    </address>
  </section>

  <section class="card card--back" aria-label="Card back">
    <svg class="card__art" viewBox="0 0 464 716">
      <defs>
        <radialGradient id="cocoaGlow">
          <stop offset="0" stop-color="#a55e51" stop-opacity="0.9"/>
          <stop offset="1" stop-color="#a55e51" stop-opacity="0"/>
        </radialGradient>
      </defs>
      <path class="field" aria-hidden="true" fill="var(--maroon)"
        d="M0,215 C60,160 200,170 270,195 C340,215 370,140 368,90 C366,40 340,10 310,0 H464 V716 H0 Z"/>
      <path class="field-edge" aria-hidden="true" fill="none" stroke="var(--cocoa)" stroke-width="7"
        d="M0,215 C60,160 200,170 270,195 C340,215 370,140 368,90 C366,40 340,10 310,0"/>
      <g role="img" aria-label="Small cocoa spiral swirl ornament">
        <circle cx="276" cy="40" r="42" fill="url(#cocoaGlow)"/>
      </g>
      <g role="img" aria-label="Cocoa spiral swirl ornament">
        <circle cx="120" cy="262" r="90" fill="url(#cocoaGlow)"/>
      </g>
    </svg>

    <div class="wordmark">MARLOW &amp; QUINCE</div>
    <p class="website">Marlow-Quince.com</p>
  </section>

</main>
</body>
</html>
```